Varnik Holdings — Business Card Design Brief
Overview
Design a double-sided business card for Varnik Holdings that highlights our two service arms: Varnik Communications (telecommunications) and Varnik Energy (business energy solutions). The card should feel smart and stand out when handed to clients.

Objectives
Showcase our areas of specialty clearly.
Reflect the overall Varnik / Varnik Holdings brand while acknowledging both arms.
Explore using both logos (Communications + Energy) or one unified logo, depending on the design.

Deliverables
One double-sided business card design (front + back).

Content & Copy
Front (preferred): Logo: Varnik / Varnik Holdings
Descriptor: Business Communications | Business Energy
Back:My contact details and company details
Core products: Business Mobile • Telephony • Internet • Business Energy Solutions

Brand & Visual Direction
We have a group logo currently tailored more toward telecoms, plus a separate Varnik Energy logo.
Please explore layouts that use both logos or just one, whichever works best.
Color: I wouldn't mind seeing an option using our the Blue/Purple gradient from our website (varnik-example.co.uk), but also open to non-gradient approaches and other colours..

Overall look: Smart, modern, and distinctive.
Format & Print Specs
Double-sided business card format. (Use a standard size

Must-Haves
Front: Varnik wording or Varnik Holdings wording with atleast 1 logo also on front “Business Communications | Business Energy.”

Back: Contact + company details and core products.
A design that stands out while remaining professional.

Nice-to-Have Options
A gradient version using our site’s Blue/Purple gradient.
A non-gradient version.
A dual-logo treatment versus a single-logo treatment.

Thanks
Owen

```html
<!DOCTYPE html>
<html lang="en">
<head>
<meta charset="utf-8">
<title>Varnik Holdings — Business Cards</title>
<link rel="stylesheet" href="https://fonts.googleapis.com/css2?family=Marcellus&display=swap">
<style>
  :root {
    --backdrop: #ece9e4;
    --card: #ffffff;
    --navy: #1f1f5e;
    --text-grey: #4a4a55;
    --rule-blue: #2aa3d8;
    --green-deep: #3fae3a;
    --green-lime: #c9d40f;
    --purple: #7a3a97;
    --indigo: #4b4fa0;
    --accent-green: #8cc63f;
    --accent-blue: #2a8fd1;
  }
  * { box-sizing: border-box; margin: 0; padding: 0; }
  html, body {
    width: 1200px; height: 900px; overflow: hidden;
    background: var(--backdrop);
    font-family: "Marcellus", "Optima", serif;
  }
  .canvas { position: relative; width: 1200px; height: 900px; }
  .card {
    position: absolute; left: 260px;
    width: 680px; height: 390px;
    background: var(--card);
    box-shadow: 0 6px 18px rgba(0,0,0,0.18);
    overflow: hidden;
  }
  .card--contact { top: 50px; }
  .card--brand { top: 480px; }
  .card__band { position: absolute; inset: 0; width: 100%; height: 100%; }

  .contact { position: absolute; left: 150px; top: 48px; color: var(--text-grey); }
  .contact__name { color: var(--navy); font-size: 21px; letter-spacing: 0.5px; }
  .contact__role { font-size: 16px; margin-top: 2px; }
  .contact__list { list-style: none; margin-top: 14px; }
  .contact__item { display: flex; align-items: center; gap: 12px; font-size: 16px; line-height: 27px; white-space: nowrap; }
  .contact__icon { width: 15px; height: 15px; flex: none; }
  .contact__rule { width: 250px; height: 1px; background: var(--rule-blue); margin: 12px 0; }
  .contact__address { font-size: 15px; line-height: 23px; }

  .products {
    position: absolute; right: 36px; bottom: 22px;
    font-size: 12px; letter-spacing: 0.4px; color: var(--navy);
    white-space: nowrap;
  }

  .lockup { position: absolute; display: flex; flex-direction: column; color: var(--navy); }
  .wordmark { display: flex; align-items: center; gap: 14px; }
  .wordmark__dot { border-radius: 50%; flex: none; }
  .wordmark__name { letter-spacing: 3px; line-height: 1; }
  .lockup__descriptor { letter-spacing: 0.6px; white-space: nowrap; }

  .card--contact .lockup { right: 36px; top: 150px; }
  .card--contact .wordmark__dot { width: 28px; height: 28px; background: var(--accent-green); }
  .card--contact .wordmark__name { font-size: 46px; }

  .card--brand .lockup { left: 240px; top: 140px; }
  .card--brand .wordmark__dot { width: 44px; height: 44px; background: var(--accent-blue); }
  .card--brand .wordmark__name { font-size: 76px; }
  .card--brand .lockup__descriptor { font-size: 17px; margin-top: 16px; margin-left: 58px; }
</style>
</head>
<body>
<main class="canvas">

  <section class="card card--contact" aria-label="Business card, contact side">
    <svg class="card__band" viewBox="0 0 680 390" aria-hidden="true">
      <defs>
        <linearGradient id="greenBand" x1="0" y1="1" x2="0.6" y2="0">
          <stop offset="0" stop-color="#3fae3a"/>
          <stop offset="0.6" stop-color="#74b82e"/>
          <stop offset="1" stop-color="#c9d40f"/>
        </linearGradient>
      </defs>
      <path d="M0 0 H95 Q30 210 210 390 H0 Z" fill="url(#greenBand)"/>
    </svg>

    <div class="contact">
      <p class="contact__name">MARCUS BELL</p>
      <p class="contact__role">Director</p>
      <ul class="contact__list">
        <li class="contact__item">
          <svg class="contact__icon" viewBox="0 0 16 16" aria-hidden="true"><rect x="4" y="1" width="8" height="14" rx="1.5" fill="none" stroke="#1f1f5e" stroke-width="1.4"/></svg>
          +44 7700 900 123
        </li>
        <li class="contact__item">
          <svg class="contact__icon" viewBox="0 0 16 16" aria-hidden="true"><path d="M3 2 L6 2 L7 5 L5 6.5 Q6.5 9.5 9.5 11 L11 9 L14 10 L14 13 Q8 14 3 8 Q2 5 3 2 Z" fill="#1f1f5e"/></svg>
          +44 0161 496 0000
        </li>
        <li class="contact__item">
          <svg class="contact__icon" viewBox="0 0 16 16" aria-hidden="true"><rect x="1" y="3" width="14" height="10" fill="#1f1f5e"/><path d="M1 3 L8 9 L15 3" fill="none" stroke="#fff" stroke-width="1.2"/></svg>
          info@varnik-example.co.uk
        </li>
        <li class="contact__item">
          <svg class="contact__icon" viewBox="0 0 16 16" aria-hidden="true"><g fill="none" stroke="#1f1f5e" stroke-width="1.1"><circle cx="8" cy="8" r="6.5"/><ellipse cx="8" cy="8" rx="3" ry="6.5"/><path d="M1.5 8 H14.5 M2.5 4.8 H13.5 M2.5 11.2 H13.5"/></g></svg>
          www.varnik-example.co.uk
        </li>
      </ul>
      <div class="contact__rule"></div>
      <p class="contact__address">24 Example Lane<br>Manchester, England, M1 0AA</p>
    </div>

    <div class="lockup">
      <div class="wordmark">
        <span class="wordmark__dot"></span>
        <span class="wordmark__name">VARNIK</span>
      </div>
    </div>

    <p class="products">Business Mobile • Telephony • Internet • Business Energy Solutions</p>
  </section>

  <section class="card card--brand" aria-label="Business card, brand side">
    <svg class="card__band" viewBox="0 0 680 390" aria-hidden="true">
      <defs>
        <linearGradient id="purpleBand" x1="0" y1="0.3" x2="1" y2="0.7">
          <stop offset="0" stop-color="#7a3a97"/>
          <stop offset="1" stop-color="#4b4fa0"/>
        </linearGradient>
      </defs>
      <path d="M0 0 H150 Q40 220 250 390 H0 Z" fill="url(#purpleBand)"/>
    </svg>

    <div class="lockup">
      <div class="wordmark">
        <span class="wordmark__dot"></span>
        <span class="wordmark__name">VARNIK</span>
      </div>
      <p class="lockup__descriptor">Business Communications | Business Energy</p>
    </div>
  </section>

</main>
</body>
</html>
```